Meridale Nutrition needs Stationary and a business card

We would like to use our current logo. The text can be moved around as needed. The stationary needs to be a 'first page' where the logo is more prominent to be impressive on higher quality paper and a second page where the logo is more subtle where there will be much more information on the page. There are 2 clinic locations which will need include name, address, phone number, fax number, web address. The business card should be single sided and contain this information also.
The design must be contemporary and sophisticated as this is a science based diet run out of a medical clinic.

Target Market(s)

People wanting to lose weight, athletes looking to optimise performance, people with arthritis or fighting cancer

Industry/Entity Type

Business

Contact Information for Business Card

must use the logo. I have attached an example card with the practice details on it. there must be space for the doctors name. Also the website www.meridalenutrition.com.au

Requirements
Must have
• the logo, the business adresses and phone numbers, the website, the doctors name and qualifications
Nice to have
• some creativity
Should not have
• Do not simply reproduce the existing card please

```html
<!DOCTYPE html>
<html lang="en">
<head>
<meta charset="utf-8">
<title>Meridale Nutrition – Business Card</title>
<link href="https://fonts.googleapis.com/css2?family=Open+Sans:wght@400;600;700&display=swap" rel="stylesheet">
<style>
  :root {
    --page-bg: #e9ebed;
    --panel-deep: #1f3f6e;
    --panel-mid: #2d5b8f;
    --panel-light: #4a7bb0;
    --accent-teal: #3aa9d6;
    --accent-line: #2a9fc9;
    --frost-light: #f1f3f4;
    --frost-mid: #d9dee2;
    --ink-navy: #1d3556;
    --text-white: #f4f7fa;
  }
  * { box-sizing: border-box; margin: 0; padding: 0; }
  html, body {
    width: 1200px; height: 970px; overflow: hidden;
    background: var(--page-bg);
    font-family: "Open Sans", Arial, sans-serif;
  }
  .business-card {
    position: absolute;
    left: 80px; top: 190px;
    width: 1040px; height: 590px;
    border-radius: 22px;
    overflow: hidden;
    background: linear-gradient(135deg, var(--frost-light), var(--frost-mid));
    box-shadow: 0 18px 40px rgba(20, 40, 70, 0.18);
  }
  .card-shapes { position: absolute; inset: 0; }
  .contact-panel {
    position: absolute; left: 52px; top: 104px;
    width: 400px;
    color: var(--text-white);
  }
  .doctor-name {
    font-size: 37px; font-weight: 400; color: var(--accent-teal);
    line-height: 1.05;
  }
  .qualifications { font-size: 26px; line-height: 1.2; }
  .address { margin-top: 86px; font-size: 27px; line-height: 1.3; }
  .contact-line {
    display: flex; align-items: center; gap: 10px;
    font-size: 28px; line-height: 1.35;
    white-space: nowrap;
  }
  .contact-line.phone { margin-top: 18px; }
  .contact-icon { width: 28px; height: 28px; flex: none; }
  .website {
    margin-top: 24px; font-size: 25px; color: var(--accent-teal);
    white-space: nowrap;
  }
  .brand-block {
    position: absolute; left: 545px; top: 0; width: 495px; height: 590px;
    display: flex; flex-direction: column; align-items: center; justify-content: center;
    gap: 28px;
  }
  .brand-circle {
    width: 150px; height: 150px; border-radius: 50%;
    background: var(--accent-teal);
  }
  .brand-name {
    font-size: 40px; font-weight: 700; color: var(--ink-navy);
    letter-spacing: 0.5px;
  }
</style>
</head>
<body>
  <div class="business-card">
    <svg class="card-shapes" width="1040" height="590" viewBox="0 0 1040 590">
      <defs>
        <linearGradient id="panelGradient" x1="0" y1="0" x2="1" y2="1">
          <stop offset="0" stop-color="var(--panel-mid)"/>
          <stop offset="0.5" stop-color="var(--panel-light)"/>
          <stop offset="1" stop-color="var(--panel-deep)"/>
        </linearGradient>
      </defs>
      <path d="M0,0 H528 C462,150 452,440 528,590 H0 Z" fill="url(#panelGradient)"/>
      <path d="M536,0 C472,150 462,440 536,590" fill="none" stroke="var(--accent-line)" stroke-width="5"/>
    </svg>

    <div class="contact-panel">
      <p class="doctor-name">Doctor’s Name</p>
      <p class="qualifications">qualifications</p>
      <p class="address">1550 Your Address, Ste B,<br>2nd Lane, LA 0000</p>
      <p class="contact-line phone">
        <svg class="contact-icon" viewBox="0 0 28 28" aria-hidden="true">
          <rect width="28" height="28" rx="4" fill="var(--accent-teal)"/>
          <path d="M9 6 l4 0 l1 5 l-2.5 1.5 a10 10 0 0 0 4 4 l1.5 -2.5 l5 1 l0 4 a2 2 0 0 1 -2 2 a15 15 0 0 1 -13 -13 a2 2 0 0 1 2 -2z" fill="var(--panel-deep)"/>
        </svg>
        0123 456 789
      </p>
      <p class="contact-line email">
        <svg class="contact-icon" viewBox="0 0 28 28" aria-hidden="true">
          <rect width="28" height="28" rx="4" fill="var(--accent-teal)"/>
          <rect x="5" y="8" width="18" height="12" fill="none" stroke="var(--panel-deep)" stroke-width="2"/>
          <path d="M5 8 l9 7 l9 -7" fill="none" stroke="var(--panel-deep)" stroke-width="2"/>
        </svg>
        info@meridale.com.au
      </p>
      <p class="website">www.meridalenutrition.com.au</p>
    </div>

    <div class="brand-block">
      <div class="brand-circle"></div>
      <p class="brand-name">Meridale Nutrition</p>
    </div>
  </div>
</body>
</html>
```